Velmarsh Group Webpage Design

We need a new website for our company. The company is Velmarsh Group Pty Ltd. We are in the business of Asbestos Removal; Demolition; Earthworks and Transport. We do not advertise and would like our website to be a reference point for our clients / potential clients and also to make our services known to those searching the internet for the services we offer. Some examples of the style of website we are after are:
http://www.quarnedemolition-example.com.au/
http://m.brintowerdemolitions-example.com.au/
http://www.fenwarddemolition-example.com.au
http://www.tolvik-example.com.au
http://www.ptrservices-example.com.au
http://www.steadfast-dismantling-example.com.au
We will need to work on content. Enclosed is an example. We also need to purchase the domain velmarshgroup-example.com.au and need to set up email accounts and ensure the website is mobile friendly. We have a company logo and have built our business on delivering professional, quality services on time. We would like the webpage to be simple, informative and professional - black and white / grey themed. We would also like to add a photo gallery etc later.

Industry/Entity Type

Construction

Coding

Coded - Design and coding required

Number of Pages Required

1 page

Colors
000000
fcfcfc
959595
dddddd

Requirements
Must have
• Information regarding the services we provide

```html
<!DOCTYPE html>
<html lang="en">
<head>
<meta charset="utf-8">
<title>Velmarsh Group</title>
<link href="https://fonts.googleapis.com/css2?family=Michroma&family=Arimo:ital,wght@0,400;0,700;1,400&display=swap" rel="stylesheet">
<style>
:root{
  --brand:#9c5752;
  --brand-soft:#a8635d;
  --grey:#959595;
  --light:#dddddd;
  --paper:#fcfcfc;
  --ink:#000000;
  --text:#444444;
}
*{margin:0;padding:0;box-sizing:border-box}
html,body{width:1200px;height:3579px;overflow:hidden}
body{position:relative;background:var(--paper);font-family:"Arimo",Arial,sans-serif;color:var(--text)}
.display{font-family:"Michroma",Arial,sans-serif;text-transform:uppercase}
.abs{position:absolute}

/* Hero */
.hero{position:absolute;left:0;top:0;width:1200px;height:656px;background:linear-gradient(180deg,#2e2d2a 0%,#4a4438 45%,#3a3630 100%)}
.hero-photo{position:absolute;inset:0;background:radial-gradient(ellipse 520px 360px at 560px 420px,rgba(190,160,60,.35),transparent 70%),radial-gradient(ellipse 300px 260px at 1050px 380px,rgba(170,140,50,.3),transparent 70%)}
.nav{position:absolute;top:24px;left:0;width:1200px;display:flex;justify-content:center;gap:46px;font-size:14px;color:#fff;letter-spacing:1px}
.nav .active{color:var(--brand-soft)}
.wordmark{position:absolute;top:176px;left:0;width:1200px;text-align:center;font-size:50px;color:var(--brand-soft);letter-spacing:4px;line-height:1}
.hero-icon{position:absolute;width:108px;height:108px;border-radius:50%;border:4px solid #fff;background:rgba(255,255,255,.08)}
.hero-icon.solid{background:#fff}
.hero-icon .glyph{position:absolute;inset:22px;border-radius:8px;background:linear-gradient(135deg,#e0b92a,#222)}
.hero-label{position:absolute;font-size:17px;color:#fff;letter-spacing:2px;width:260px;text-align:center}
.dots{position:absolute;display:flex;gap:14px;align-items:center}
.dots span{width:7px;height:7px;border-radius:50%;background:var(--brand-soft)}
.dots span.on{width:14px;height:14px;border:2px solid #ccc;background:transparent}

/* Welcome */
.welcome-title{position:absolute;top:716px;left:0;width:1200px;text-align:center;font-size:30px;font-weight:400;color:#222;letter-spacing:3px}
.welcome-title em{font-style:normal;color:var(--brand-soft)}
.welcome-text{position:absolute;top:768px;left:190px;width:820px;text-align:center;font-size:13px;line-height:26px;color:#555}
.btn-grey{position:absolute;background:#8e8e8e;color:#fff;font-size:15px;letter-spacing:2px;display:flex;align-items:center;justify-content:center}

/* Services */
.services{position:absolute;top:971px;left:0;width:1200px;height:551px;background:linear-gradient(135deg,#2d2b29 0%,#3c3834 50%,#2a2826 100%)}
.person{position:absolute;left:0;top:943px;width:286px;height:579px;background:linear-gradient(180deg,#c9a78e 0%,#8d8d8d 30%,#6f7378 70%,#4d6a8a 100%)}
.diamond{position:absolute;width:88px;height:88px;background:var(--brand);transform:rotate(45deg);border:3px solid #fff}
.svc-title{position:absolute;font-size:16px;color:var(--brand-soft);letter-spacing:2px;text-decoration:underline;width:318px;text-align:center}
.svc-text{position:absolute;left:325px;top:1217px;width:318px;text-align:center;color:#fff;font-size:13px;line-height:28px}
.btn-brand{position:absolute;background:var(--brand);color:#fff;font-size:14px;letter-spacing:2px;display:flex;align-items:center;justify-content:center}
.tile{position:absolute;width:198px;height:198px;border:2px solid #ddd;color:#fff;font-size:13px;letter-spacing:1px;text-align:center}
.tile.active{background:var(--brand);border-color:var(--brand)}
.tile .mark{position:absolute;left:66px;top:36px;width:66px;height:66px;border-radius:50%;border:3px solid #fff;background:var(--brand)}
.tile .mark.diamond-mark{border-radius:4px;transform:rotate(45deg);width:58px;height:58px;left:70px;top:40px}
.tile .label{position:absolute;left:0;right:0;top:134px;line-height:24px}

/* Testimonial */
.testimonial{position:absolute;top:1522px;left:0;width:1200px;height:478px;background:linear-gradient(180deg,#a0625c 0%,#9c5d57 55%,#8a4f4a 100%)}
.avatar{position:absolute;border-radius:50%;border:4px solid #fff;background:linear-gradient(160deg,#d8c1b2,#7b5f55)}
.person-name{position:absolute;top:1766px;left:0;width:1200px;text-align:center;color:#fff;font-size:17px;letter-spacing:2px}
.person-role{position:absolute;top:1800px;left:0;width:1200px;text-align:center;color:#fff;font-size:9px;letter-spacing:2px}
.quote{position:absolute;top:1842px;left:220px;width:760px;text-align:center;color:#fff;font-style:italic;font-size:13px;line-height:24px}

/* Gallery */
.gallery-title{position:absolute;top:2062px;left:0;width:1200px;text-align:center;font-size:26px;font-weight:400;color:#222;letter-spacing:5px}
.shot{position:absolute}
.shot.framed::after{content:"";position:absolute;inset:-6px;border:6px solid rgba(140,140,140,.85)}

/* Contact */
.contact{position:absolute;top:2806px;left:0;width:1200px;height:630px;background:linear-gradient(180deg,#2c3236 0%,#47484a 60%,#393a3c 100%)}
.contact-title{position:absolute;top:2866px;left:0;width:1200px;text-align:center;font-size:28px;font-weight:400;color:#fff;letter-spacing:4px}
.col-head{position:absolute;top:2960px;font-size:15px;color:#fff;letter-spacing:2px;width:400px;text-align:center}
.field{position:absolute;left:79px;width:496px;background:#fff;font-size:12px;color:#777;padding:12px 14px}
.field.first{border:2px solid #3cc7d3}
.submit{position:absolute;left:265px;top:3264px;width:124px;height:124px;border-radius:50%;background:var(--brand);color:#fff;font-size:16px;letter-spacing:2px;display:flex;align-items:center;justify-content:center}
.detail-name{position:absolute;left:726px;font-size:13px;color:#fff;letter-spacing:1px}
.detail-name i{font-family:"Arimo",Arial,sans-serif;text-transform:none;letter-spacing:0;font-size:15px}
.detail-line{position:absolute;left:726px;font-size:14px;color:#eee;display:flex;align-items:center;gap:16px}
.detail-line svg{width:18px;height:18px;flex:none}

/* Footer */
.footer{position:absolute;top:3436px;left:0;width:1200px;height:143px;background:var(--brand)}
.social{position:absolute;width:40px;height:40px;border:2px solid #fff;transform:rotate(45deg)}
.copyright{position:absolute;top:3540px;left:0;width:1200px;text-align:center;color:#fff;font-size:11px;letter-spacing:2px}
</style>
</head>
<body>

<header class="hero">
  <div class="hero-photo" role="img" aria-label="Mining dump truck and excavator on an earthworks site"></div>
  <nav class="nav display">
    <span class="active">Home</span><span>About Us</span><span>Services</span><span>Safety</span><span>Environment</span><span>Contact Us</span>
  </nav>
  <div class="wordmark display">Velmarsh Group</div>

  <div class="hero-label display" style="left:470px;top:340px">Demolition</div>
  <div class="hero-icon solid" style="left:296px;top:352px" role="img" aria-label="Transport truck icon"><div class="glyph"></div></div>
  <div class="hero-icon" style="left:546px;top:382px" role="img" aria-label="Demolition excavator icon"><div class="glyph" style="background:linear-gradient(135deg,#ddd,#555)"></div></div>
  <div class="hero-icon solid" style="left:796px;top:352px" role="img" aria-label="Earthmoving excavator icon"><div class="glyph"></div></div>
  <div class="hero-label display" style="left:220px;top:506px">Transport</div>
  <div class="hero-label display" style="left:720px;top:506px">Earthmoving</div>

  <div class="dots" style="left:548px;top:604px"><span class="on"></span><span></span><span></span><span></span></div>
</header>

<section class="welcome">
  <h1 class="welcome-title display">Welcome to the <em>Velmarsh Group</em></h1>
  <p class="welcome-text">Velmarsh Transport Pty Ltd was established by Director Daniel Harwick in 2002 with a focus providing services within the transport industry. Over time the company has developed and expanded to include the provision of Earthworks and Demolition. Daniel has over 10 years' experience working at all levels within these industries focusing primarily on Demolition...</p>
  <div class="btn-grey display" style="left:496px;top:866px;width:208px;height:52px">Read More</div>
</section>

<section class="services" role="img" aria-label="Dark quarry landscape background"></section>
<div class="person" role="img" aria-label="Smiling company representative with arms folded"></div>
<div class="diamond" style="left:433px;top:1042px"></div>
<div class="abs" style="left:455px;top:1064px;width:44px;height:44px;border:3px solid #fff;border-radius:50%"></div>
<div class="svc-title display" style="left:325px;top:1178px">Demolition</div>
<p class="svc-text">Velmarsh Transport and Demolition provide an extensive range of demolition services. A large amount of experience across a broad range of projects results in a dependable service and peace of mind for all clients. Services include:<br>•&nbsp;&nbsp;&nbsp;Commercial Demolition</p>
<div class="btn-brand display" style="left:384px;top:1415px;width:191px;height:38px">Read More</div>

<div class="tile active display" style="left:706px;top:1038px"><div class="mark"></div><div class="label">Demolition</div></div>
<div class="tile display" style="left:926px;top:1038px"><div class="mark"></div><div class="label">Earthworks</div></div>
<div class="tile display" style="left:706px;top:1257px"><div class="mark diamond-mark"></div><div class="label">Asbestos</div></div>
<div class="tile display" style="left:926px;top:1257px"><div class="mark"></div><div class="label" style="top:124px">Hours of<br>Operation</div></div>

<section class="testimonial" role="img" aria-label="Reddish tinted city rooftop background"></section>
<div class="avatar" style="left:403px;top:1584px;width:84px;height:84px" role="img" aria-label="Client portrait"></div>
<div class="avatar" style="left:538px;top:1615px;width:124px;height:124px" role="img" aria-label="Client portrait"></div>
<div class="avatar" style="left:715px;top:1584px;width:84px;height:84px" role="img" aria-label="Client portrait"></div>
<div class="person-name display">Nora Bellamy</div>
<div class="person-role display">Writer &amp; Blogger, Canada</div>
<p class="quote">"Lorem Ipsum is simply dummy text of the printing and typesetting industry. Lorem Ipsum has been the industry's standard dummy text ever since the 1500s, when an unknown printer took a galley of type and scrambled it to make a type specimen book."</p>
<div class="dots" style="left:553px;top:1962px"><span class="on" style="width:10px;height:10px"></span><span style="background:#ddd"></span><span style="background:#ddd"></span><span style="background:#ddd"></span><span style="background:#ddd"></span></div>

<section class="gallery">
  <h2 class="gallery-title display">Our Gallery</h2>
  <div class="shot framed" style="left:86px;top:2140px;width:188px;height:174px;background:linear-gradient(135deg,#d49a55,#8a5a2e)" role="img" aria-label="Hard hats and tools"></div>
  <div class="shot" style="left:282px;top:2140px;width:358px;height:174px;background:linear-gradient(135deg,#c9d6de,#b84a3a 55%,#8a7566)" role="img" aria-label="Bricklayer in red overalls"></div>
  <div class="shot" style="left:647px;top:2140px;width:200px;height:174px;background:linear-gradient(180deg,#5a9ad6,#c7a04c)" role="img" aria-label="Construction cranes against blue sky"></div>
  <div class="shot" style="left:854px;top:2140px;width:263px;height:174px;background:linear-gradient(180deg,#4f8bc7,#c9a23a 60%,#7a5b3a)" role="img" aria-label="Yellow dump truck in quarry"></div>

  <div class="shot" style="left:86px;top:2319px;width:188px;height:162px;background:linear-gradient(135deg,#9a8b7a,#c3a57a)" role="img" aria-label="Truck unloading soil"></div>
  <div class="shot" style="left:282px;top:2319px;width:262px;height:162px;background:linear-gradient(180deg,#b9c5cf,#c7a981)" role="img" aria-label="Sand piles on a building site"></div>
  <div class="shot" style="left:551px;top:2319px;width:272px;height:162px;background:linear-gradient(135deg,#d7d7d7,#8a6e4e 60%,#3d3d3d)" role="img" aria-label="Worker building a concrete form"></div>
  <div class="shot" style="left:830px;top:2319px;width:287px;height:162px;background:linear-gradient(180deg,#7fb0dc,#d8a52a 55%,#6b8a3a)" role="img" aria-label="Excavator digging"></div>

  <div class="shot" style="left:86px;top:2493px;width:253px;height:179px;background:linear-gradient(180deg,#8d8d8d,#4f4a44)" role="img" aria-label="Workers overlooking a mine"></div>
  <div class="shot" style="left:346px;top:2493px;width:267px;height:179px;background:linear-gradient(135deg,#6d7f96,#a25a3a 55%,#3a2e28)" role="img" aria-label="Demolished building rubble"></div>
  <div class="shot" style="left:620px;top:2493px;width:224px;height:179px;background:linear-gradient(180deg,#e7a43a,#7a4a1a 70%,#222)" role="img" aria-label="Crane silhouettes at sunset"></div>
  <div class="shot" style="left:851px;top:2493px;width:266px;height:179px;background:linear-gradient(135deg,#8a8a8a,#c6b06a 50%,#3f4a6a)" role="img" aria-label="Worker using a jackhammer"></div>

  <div class="btn-grey display" style="left:496px;top:2701px;width:208px;height:53px">View All</div>
</section>

<section class="contact" role="img" aria-label="City skyline at dusk background"></section>
<h2 class="contact-title display">Contact Us</h2>
<div class="col-head display" style="left:130px">Inquiry Form</div>
<div class="col-head display" style="left:672px">Company Detail</div>

<div class="field first" style="top:3006px;height:52px">Enter Name:</div>
<div class="field" style="top:3068px;height:51px">Enter Phone no.:</div>
<div class="field" style="top:3130px;height:52px">Enter E-Mail:</div>
<div class="field" style="top:3195px;height:131px">Message:</div>
<div class="submit display">Submit</div>

<div class="detail-name display" style="top:3010px">Daniel Harwick, <i>Director</i></div>
<div class="detail-line" style="top:3057px"><svg viewBox="0 0 20 20"><path d="M10 1a6 6 0 0 0-6 6c0 5 6 12 6 12s6-7 6-12a6 6 0 0 0-6-6z" fill="#b35a52"/><circle cx="10" cy="7" r="2.2" fill="#fff"/></svg>PO Box 512 KELDARRA QLD 4391</div>
<div class="detail-line" style="top:3093px"><svg viewBox="0 0 20 20"><rect x="1" y="4" width="18" height="12" fill="#b35a52"/><path d="M1 4l9 7 9-7" stroke="#fff" stroke-width="1.5" fill="none"/></svg>info@velmarshdemo-example.com</div>
<div class="detail-line" style="top:3129px"><svg viewBox="0 0 20 20"><path d="M4 2l4 1 1 4-2 2a11 11 0 0 0 4 4l2-2 4 1 1 4-2 2C9 18 2 11 2 4z" fill="#b35a52"/></svg>0400 555 213</div>

<div class="detail-name display" style="top:3186px">Leah Tamsin, <i>Administration</i></div>
<div class="detail-line" style="top:3236px"><svg viewBox="0 0 20 20"><path d="M10 1a6 6 0 0 0-6 6c0 5 6 12 6 12s6-7 6-12a6 6 0 0 0-6-6z" fill="#b35a52"/><circle cx="10" cy="7" r="2.2" fill="#fff"/></svg>PO Box 512 KELDARRA QLD 4391</div>
<div class="detail-line" style="top:3272px"><svg viewBox="0 0 20 20"><rect x="1" y="4" width="18" height="12" fill="#b35a52"/><path d="M1 4l9 7 9-7" stroke="#fff" stroke-width="1.5" fill="none"/></svg>info@velmarshdemo-example.com</div>
<div class="detail-line" style="top:3308px"><svg viewBox="0 0 20 20"><path d="M4 2l4 1 1 4-2 2a11 11 0 0 0 4 4l2-2 4 1 1 4-2 2C9 18 2 11 2 4z" fill="#b35a52"/></svg>0400 555 876</div>

<footer class="footer">
  <svg class="abs" style="left:560px;top:-48px" width="80" height="50" viewBox="0 0 80 50"><path d="M0 50L40 10l40 40z" fill="#9c5752"/><path d="M31 36l9-8 9 8M31 44l9-8 9 8" stroke="#fff" stroke-width="3" fill="none"/></svg>
  <div class="social" style="left:522px;top:30px"></div>
  <div class="social" style="left:581px;top:30px"></div>
  <div class="social" style="left:640px;top:30px"></div>
</footer>
<div class="copyright display">© Velmarsh Group - 2015. All rights reserved.</div>

</body>
</html>
```